New business card/stationary for a consulting company

I am looking for a clean and very professional looking business card for my consulting company as well as corresponding stationary. I am uploading our logo. I like simple and powerful for the feel. No graphics but I am open on everything else. Below is my contact information but would like the final to be in a version I can add my employees information into and print. Thank you.

Daniel Whitcombe
dan@ferncliffadvisory.com
2870 North 9th Avenue, Summit Floor, Elm Ridge, Illinois 60531
www.ferncliffadvisory.com

Industry/Entity Type

Consulting

Contact Information for Business Card

Daniel Whitcombe
dan@ferncliffadvisory.com
www.ferncliffadvisory.com

Font styles to use
Serif
Sans Serif

Requirements
Must have
• Our logo and the business card details.
Nice to have
• our website www.ferncliffadvisory.com

```html
<!DOCTYPE html>
<html lang="en">
<head>
<meta charset="utf-8">
<title>Ferncliff Advisory – Business Card</title>
<link rel="stylesheet" href="https://fonts.googleapis.com/css2?family=Marcellus&family=Roboto:wght@400&display=swap">
<style>
  :root {
    --navy: #142c5e;
    --ink: #2a2a2a;
    --paper: #f4f4f3;
    --backdrop: #e4e4e4;
    --white: #ffffff;
  }
  html, body {
    margin: 0;
    width: 1200px;
    height: 576px;
    overflow: hidden;
    background: var(--backdrop);
  }
  .stage { position: relative; width: 1200px; height: 576px; }
  .card {
    position: absolute;
    top: 139px;
    height: 291px;
    border-radius: 13px;
    overflow: hidden;
  }
  .card-front { left: 82px; width: 484px; background: var(--navy); }
  .card-back { left: 602px; width: 480px; background: var(--paper); }

  .front-mark {
    position: absolute;
    left: 50%;
    top: 106px;
    width: 40px;
    height: 40px;
    margin-left: -20px;
    background: var(--white);
  }
  .front-name {
    position: absolute;
    left: 0; right: 0;
    top: 162px;
    text-align: center;
    font-family: "Marcellus", serif;
    font-size: 26px;
    letter-spacing: 1.5px;
    color: var(--white);
    text-transform: uppercase;
  }

  .back-mark {
    position: absolute;
    left: 35px; top: 44px;
    width: 62px; height: 62px;
    background: var(--navy);
  }
  .back-name {
    position: absolute;
    left: 190px; top: 46px;
    width: 200px;
    text-align: center;
    font-family: "Marcellus", serif;
    font-size: 22px;
    line-height: 28px;
    letter-spacing: 1px;
    color: var(--navy);
    text-transform: uppercase;
  }
  .person-name {
    position: absolute;
    left: 28px; top: 134px;
    font-family: "Marcellus", serif;
    font-size: 18px;
    letter-spacing: 1px;
    color: var(--navy);
    text-transform: uppercase;
  }
  .swoosh { position: absolute; inset: 0; }
  .contact {
    position: absolute;
    right: 18px; top: 190px;
    margin: 0;
    font-family: "Roboto", sans-serif;
    font-size: 12px;
    color: var(--white);
    text-align: right;
    font-style: normal;
    line-height: 20px;
  }
  .contact .line { display: flex; justify-content: flex-end; align-items: center; gap: 6px; }
  .contact .address { margin-top: 4px; }
  .contact svg { width: 9px; height: 9px; }
</style>
</head>
<body>
<main class="stage">
  <section class="card card-front" aria-label="Card front">
    <div class="front-mark"></div>
    <div class="front-name">Ferncliff Advisory</div>
  </section>

  <section class="card card-back" aria-label="Card back">
    <svg class="swoosh" viewBox="0 0 480 291" width="480" height="291" aria-hidden="true">
      <path d="M0,250 C110,292 270,236 480,124 L480,291 L0,291 Z" fill="var(--navy)"/>
      <path d="M0,198 C100,262 260,250 480,101 L480,116 C260,268 90,272 0,236 Z" fill="var(--ink)"/>
      <path d="M0,236 C90,272 220,270 340,232 C230,276 90,282 0,246 Z" fill="var(--ink)"/>
    </svg>
    <div class="back-mark"></div>
    <div class="back-name">Ferncliff<br>Advisory</div>
    <div class="person-name">Daniel Whitcombe</div>
    <address class="contact">
      <div class="line">ferncliffadvisory.com
        <svg viewBox="0 0 10 10"><circle cx="5" cy="5" r="4.3" fill="none" stroke="#fff" stroke-width="1"/><ellipse cx="5" cy="5" rx="1.8" ry="4.3" fill="none" stroke="#fff" stroke-width="0.8"/><line x1="0.7" y1="5" x2="9.3" y2="5" stroke="#fff" stroke-width="0.8"/></svg>
      </div>
      <div class="line">dan@ferncliffadvisory.com
        <svg viewBox="0 0 10 10"><rect x="0.5" y="2" width="9" height="6.5" fill="none" stroke="#fff" stroke-width="1"/><path d="M0.5,2 L5,6 L9.5,2" fill="none" stroke="#fff" stroke-width="1"/></svg>
      </div>
      <div class="address">2870 North 9th Avenue, Summit Floor,<br>Elm Ridge, Illinois 60531</div>
    </address>
  </section>
</main>
</body>
</html>
```